Graphic Design Project

ok I have the artwork for my presentation folder, and I have the text to put on the folder, I need you to apply text to the folder and the single sheets, so inside the artwork is pictures to use, text to use. thank you so much ask me as many questions as you need
Updates

my girl forgot to upload the mock ups of the presentation folder and single sheets, my apologies please check updated files

Hey Guys this is a eazy project the artwork is done, the text is done, the pictures are done!, all you have to do is assemble the project, I even have mock up pictures of how project looks finished, I have made the money good so that you would not pass on this project because it is not that creative of a job!

Target Market(s)

Dr's and patients

Industry/Entity Type

Graphic Design

Requirements
Must have
• use the single sheet artwork to make as many single sheets as you need to use all of the text supplied
Should not have
• do not make this, so professional looking that it does not appeal to the patients

```html
<!DOCTYPE html>
<html lang="en">
<head>
<meta charset="utf-8">
<title>KindPath Counseling – Information Sheet</title>
<link rel="stylesheet" href="https://fonts.googleapis.com/css2?family=Libre+Baskerville:wght@400;700&display=swap">
<style>
  :root {
    --paper: #ffffff;
    --panel-grey: #d1d2d4;
    --sand: #d6cfbd;
    --ink: #1e1e1e;
    --brand-ink: #1a1a1a;
    --photo-warm: #c9a66b;
    --photo-dark: #4a4036;
    --photo-blue: #3c4f5c;
  }
  * { margin: 0; padding: 0; box-sizing: border-box; }
  html, body { width: 927px; height: 1200px; overflow: hidden; background: var(--paper); }
  .sheet { position: relative; width: 927px; height: 1200px; overflow: hidden; background: var(--paper); }
  .backdrop { position: absolute; inset: 0; width: 927px; height: 1200px; }
  .sheet-title {
    position: absolute; top: 50px; left: 0; width: 927px;
    text-align: center;
    font-family: "Libre Baskerville", serif;
    font-weight: 700; font-size: 40px; color: var(--brand-ink);
  }
  .sheet-copy {
    position: absolute; top: 120px; left: 57px; width: 822px;
    font-family: "Libre Baskerville", serif;
    font-size: 19.2px; line-height: 25.8px; color: var(--ink);
    hyphens: auto;
  }
  .sheet-copy p { margin-bottom: 25.6px; }
  .brand { font-weight: 700; color: var(--brand-ink); }
</style>
</head>
<body>
<main class="sheet">
  <svg class="backdrop" viewBox="0 0 927 1200" aria-hidden="false">
    <defs>
      <linearGradient id="photoTone" x1="0" y1="0" x2="1" y2="1">
        <stop offset="0" stop-color="var(--photo-blue)"/>
        <stop offset="0.35" stop-color="var(--photo-warm)"/>
        <stop offset="0.6" stop-color="#d9b48f"/>
        <stop offset="1" stop-color="var(--photo-dark)"/>
      </linearGradient>
    </defs>
    <path class="panel-grey" fill="var(--panel-grey)"
      d="M0,0 H736 L927,64 V330 L828,862 Q820,892 790,886 L0,688 Z"/>
    <path class="accent-sand" fill="var(--sand)"
      d="M927,606 Q912,606 906,628 L818,960 Q810,990 840,996 L927,1034 Z"/>
    <path class="accent-grey" fill="var(--panel-grey)"
      d="M810,1072 Q790,1068 786,1090 L760,1200 H927 V1092 Z"/>
    <path class="feature-photo" fill="url(#photoTone)" role="img"
      aria-label="Photo: close-up of two people gently holding hands, warm autumn light"
      d="M0,712 L758,944 Q786,954 782,982 L752,1200 H0 Z"/>
  </svg>

  <h1 class="sheet-title">KindPath Counseling</h1>

  <section class="sheet-copy">
    <p><span class="brand">KindPath Counseling</span> will provide education, assessments, prevention and screening for those individuals with chronic pain and substance use disorders.</p>
    <p><span class="brand">KindPath Counseling</span> is a proactive addiction counseling center dedicated to addressing health issues in an integrated manner by working with pain management physicians to offer opioid education to prevent substance use and misuse disorders to their patients.</p>
    <p>Many Pain Management Clinics and primary care physicians are interested in Reducing Risk to their Patients and Practice from opioid misuse and increasing quality care for their patients. Physicians are Excited to have a service like <span class="brand">KindPath Counseling</span> to provide education and screening services for their Patients.</p>
    <p><span class="brand">KindPath Counseling</span> services are provided by Highly Trained and Caring Professionals who are experienced in working in all areas of Patient Education, Prevention and Care.</p>
    <p><span class="brand">KindPath Counseling</span> is a resource for Pain Management Clinics and Primary Care Physicians to Educate, Assess and provide Prevention and Counseling to Patients to Reduce the Risk of substance use disorders.</p>
  </section>
</main>
</body>
</html>
```